Business Card for Multi-Brand Sportswear Company

We are looking for a business card which represents our company and the multiple brands within it.

The company: Fen Athletics (LTD)
The brands: Fen, TavaPuni, ElmStretch, Grit and Rain

Employees using these cards would be representing Fen Athletics, rather than any of the individual brands. You will see a current design within the uploaded files, to give some inspiration. The actual text of the brands is not necessary, but the logos should be on there is some format.

Our creative minds on this are stretched, so we are looking for someone to make this their own, and show us what a good business card should look like.

We may like to get these printed with spot gloss, so keep that in mind with your designs.

www.fenathletics.co.uk

Industry/Entity Type

Business

Contact Information for Business Card

Leo Pemberton-Hale
Operations Manager
(+44) 1632 960 418
Leo@fenathletics.co.uk
www.fenathletics.co.uk

Font styles to use
Sans Serif
Other font styles liked:
• Eurostile

Colors
ffffff

Requirements
Nice to have
• Dark (black) background

```html
<!DOCTYPE html>
<html lang="en">
<head>
<meta charset="utf-8">
<title>Fen Athletics – Business Card</title>
<link rel="stylesheet" href="https://fonts.googleapis.com/css2?family=Saira:wght@400;500;600&display=swap">
<style>
  :root {
    --page-bg: #ececec;
    --card-light: #f4f4f4;
    --card-light-edge: #e2e2e2;
    --card-dark: #2b2b2b;
    --card-dark-edge: #1f1f1f;
    --ink: #111111;
    --ink-soft: #3a3a3a;
    --white: #ffffff;
    --accent: #e3232b;
  }
  * { box-sizing: border-box; margin: 0; padding: 0; }
  html, body {
    width: 1200px;
    height: 586px;
    overflow: hidden;
    background: var(--page-bg);
    font-family: "Saira", sans-serif;
  }
  .stage { position: relative; width: 1200px; height: 586px; }

  .card {
    position: absolute;
    top: 129px;
    width: 502px;
    height: 300px;
    overflow: hidden;
  }
  .card-front { left: 65px; }
  .card-back { left: 608px; }

  .card-texture {
    position: absolute;
    inset: 0;
  }
  .card-front .card-texture {
    background: linear-gradient(135deg, var(--card-light) 0%, var(--white) 45%, var(--card-light-edge) 100%);
  }
  .card-back .card-texture {
    background: linear-gradient(135deg, var(--card-dark) 0%, #333333 50%, var(--card-dark-edge) 100%);
  }

  /* Front: company lockup */
  .company-lockup {
    position: absolute;
    left: 41px;
    top: 108px;
    width: 422px;
    text-align: right;
  }
  .company-name {
    display: flex;
    align-items: center;
    justify-content: center;
    gap: 14px;
    font-size: 46px;
    font-weight: 500;
    line-height: 1;
    letter-spacing: 2px;
    color: var(--ink);
  }
  .company-name .mark-square {
    width: 22px;
    height: 22px;
    background: var(--accent);
  }
  .company-tagline {
    margin-top: 6px;
    text-align: center;
    padding-left: 36px;
    font-size: 11px;
    letter-spacing: 2.6px;
    color: var(--ink-soft);
  }

  .brand-row {
    position: absolute;
    left: 0;
    right: 0;
    top: 242px;
    display: flex;
    justify-content: center;
    gap: 16px;
    font-size: 12px;
    font-weight: 500;
    color: var(--ink-soft);
    letter-spacing: 0.5px;
  }

  /* Back: contact */
  .person {
    position: absolute;
    right: calc(502px - 206px);
    top: 140px;
    text-align: right;
    color: var(--white);
  }
  .person-name {
    font-size: 17px;
    font-weight: 600;
    line-height: 1.1;
  }
  .person-role {
    margin-top: 3px;
    font-size: 11.5px;
    color: #e4e4e4;
  }

  .divider {
    position: absolute;
    left: 242px;
    top: 103px;
    width: 2px;
    height: 120px;
    background: linear-gradient(to bottom, transparent, var(--accent) 35%, var(--accent) 65%, transparent);
  }

  .contact-list {
    position: absolute;
    left: 276px;
    top: 108px;
    list-style: none;
    color: var(--white);
    font-size: 12px;
  }
  .contact-list li {
    display: flex;
    align-items: center;
    gap: 8px;
    height: 16px;
    margin-bottom: 8.5px;
  }
  .contact-list svg { width: 13px; height: 13px; flex: none; }

  .address {
    position: absolute;
    left: 276px;
    top: 184px;
    font-size: 13.5px;
    font-weight: 600;
    line-height: 17px;
    color: var(--white);
  }
</style>
</head>
<body>
<main class="stage">

  <section class="card card-front" aria-label="Business card front">
    <div class="card-texture" role="img" aria-label="Light faceted geometric background texture"></div>
    <div class="company-lockup">
      <div class="company-name"><span class="mark-square"></span>FEN ATHLETICS</div>
      <div class="company-tagline">PERFORMANCE WEAR</div>
    </div>
    <div class="brand-row">
      <span>TavaPuni</span>
      <span>ElmStretch</span>
      <span>Grit and Rain</span>
      <span>Fen</span>
    </div>
  </section>

  <section class="card card-back" aria-label="Business card back">
    <div class="card-texture" role="img" aria-label="Dark faceted geometric background texture"></div>

    <div class="person">
      <div class="person-name">Leo Pemberton-Hale</div>
      <div class="person-role">Managing Director</div>
    </div>

    <div class="divider"></div>

    <ul class="contact-list">
      <li>
        <svg viewBox="0 0 16 16" aria-hidden="true"><path fill="#e3232b" d="M1 5c0-2 3-3 7-3s7 1 7 3v1h-4V5H5v1H1zM4 7h8l2 6H2z"/><circle cx="8" cy="10" r="1.5" fill="#2b2b2b"/></svg>
        <span>+44 (0)1632 960418</span>
      </li>
      <li>
        <svg viewBox="0 0 16 16" aria-hidden="true"><path fill="#e3232b" d="M4 1h8v4H4zM1 6h14v6h-3v3H4v-3H1z"/><rect x="5" y="10" width="6" height="3" fill="#2b2b2b"/></svg>
        <span>(713) 555-0142</span>
      </li>
      <li>
        <svg viewBox="0 0 16 16" aria-hidden="true"><rect x="1" y="3" width="14" height="10" fill="#e3232b"/><path d="M1 3l7 6 7-6" fill="none" stroke="#2b2b2b" stroke-width="1.3"/></svg>
        <span>leo@fenathletics.co.uk</span>
      </li>
    </ul>

    <address class="address" style="font-style: normal;">
      Lower Mead, Ashbyfield<br>
      Carrow, ZZ9 4QX
    </address>
  </section>

</main>
</body>
</html>
```